Professional Website for Leading Global Private Equity Real Estate Company

The company is a leading global Private Equity Real Estate (PERE). We need a homepage design, an inner page design, and color/font tweaks to the logo (color should be more soothing than current blue used in the logo). The logo website should project the company as global, professional, experienced, trustworthy, accessible, YOUNG, DYNAMIC, hi-tech. PLEASE SEE the attached Design Brief Word Doc for details.

Target Market(s)

institional investors and wealthy private individuals

Industry/Entity Type

Finance

Number of Pages Required

2 page

Font styles to use
Sans Serif
Other font styles liked:
• either like in https://www.ferndalequay.com/ or like in presentations (Montserrat Black & Montserrat Light, Century Gothic, Blair ITC, Almoni Neue DL 4.0 AAA Medium, Almoni DL AAA)

Requirements
Must have
• new color palette that is NOT based on current logo. they want a more soothing color palette than the blue in that logo. the new color palette should project: global, professional, experienced, trustworthy, accessible, YOUNG, DYNAMIC, hi-tech.
Nice to have
• the likes these sites: https://www.ferndalequay.com/ and https://www.tvr.law/

```html
<!DOCTYPE html>
<html lang="en">
<head>
<meta charset="utf-8">
<title>Corvana Real Estate — Global Private Equity Real Estate</title>
<link href="https://fonts.googleapis.com/css2?family=Montserrat:wght@300;400;500;600;700&family=Questrial&display=swap" rel="stylesheet">
<style>
:root{
  --sky:#3cc3f2;
  --sky-deep:#16a6e0;
  --sky-soft:#bfe9fa;
  --pale:#eef9fe;
  --ink:#1c1c1e;
  --muted:#6d7480;
  --white:#ffffff;
  --line:#d7eef8;
}
*{box-sizing:border-box;margin:0;padding:0}
html,body{width:1200px;height:4204px;overflow:hidden}
body{position:relative;background:var(--white);font-family:"Montserrat",sans-serif;color:var(--ink)}
.abs{position:absolute}
.display{font-family:"Questrial",sans-serif}
.btn{position:absolute;display:flex;align-items:center;gap:10px;background:var(--sky);color:var(--white);border-radius:22px;font-size:13px;font-weight:600;text-transform:uppercase;padding:0 6px 0 20px;height:34px;letter-spacing:.5px}
.btn .dot{width:26px;height:26px;border-radius:50%;background:var(--white);display:flex;align-items:center;justify-content:center}
.para{font-size:13px;line-height:1.7;color:var(--muted)}
.photo{position:absolute;overflow:hidden}

/* nav */
.nav{position:absolute;left:0;top:0;width:1200px;height:70px;z-index:3}
.brand{position:absolute;left:36px;top:22px;display:flex;align-items:center;gap:8px;font-size:20px;font-weight:600;color:var(--sky-deep)}
.brand i{width:22px;height:22px;border-radius:50%;background:var(--sky);display:block}
.menu{position:absolute;left:490px;top:28px;display:flex;gap:22px;font-size:11px;font-weight:500;text-transform:uppercase}
.menu span:first-child{color:var(--sky-deep);border-bottom:2px solid var(--sky)}
.login{position:absolute;left:1026px;top:20px;width:106px;height:32px;border-radius:16px;background:var(--sky);color:var(--white);font-size:12px;font-weight:600;display:flex;align-items:center;justify-content:center;gap:8px}

/* hero */
.hero-bg{position:absolute;left:-160px;top:-220px;width:880px;height:860px;border-radius:50%;background:var(--pale)}
.hero-photo{left:30px;top:70px;width:600px;height:520px;border-radius:0 0 300px 300px;background:linear-gradient(140deg,#8fa3b6,#d9e2ea 45%,#5d6a78);}
.play{position:absolute;width:56px;height:56px;border-radius:50%;background:var(--white);display:flex;align-items:center;justify-content:center;box-shadow:0 4px 14px rgba(0,0,0,.15)}
.hero-text{left:630px;top:236px}
.hero-text .kicker{font-size:17px;font-weight:500}
.hero-text h1{font-family:"Questrial",sans-serif;font-weight:400;font-size:56px;line-height:1.02;text-transform:uppercase;margin-top:10px;letter-spacing:1px}
.hero-text h1 em{font-style:normal;color:var(--sky)}
.play-video{left:1000px;top:600px;display:flex;align-items:center;gap:14px;font-size:12px}

/* stats */
.stats{left:190px;top:640px;width:880px;display:flex;justify-content:space-between;text-align:center}
.stat b{display:block;font-family:"Questrial",sans-serif;font-weight:400;font-size:34px;color:var(--sky-deep)}
.stat small{display:block;font-size:10px;font-weight:600;margin-top:2px}
.stat span{display:block;font-size:11px;color:var(--muted);margin-top:4px}

/* about */
.about{left:180px;top:950px;width:420px}
.about h3{font-size:14px;font-weight:600}
.about h2{font-family:"Questrial",sans-serif;font-weight:400;font-size:38px;margin:6px 0 18px}
.about h2 span{color:var(--sky)}
.checks{list-style:none;margin-top:16px}
.checks li{display:flex;align-items:center;gap:10px;font-size:12px;color:var(--muted);margin-bottom:10px}
.checks li i{width:14px;height:14px;background:var(--sky);display:block;border-radius:2px}
.about-art{left:690px;top:970px;width:400px;height:300px;border-radius:8px;background:radial-gradient(circle at 50% 60%,#f3f5f7,#e3e8ec 70%)}

/* platforms */
.platforms{left:0;top:1400px;width:1200px;height:940px;background:linear-gradient(180deg,#f4fbfe,#d8f1fc)}
.platforms h2{position:absolute;left:0;width:1200px;top:80px;text-align:center;font-family:"Questrial",sans-serif;font-weight:400;font-size:38px}
.platforms h2 span{display:block;color:var(--sky)}
.center-photo{left:470px;top:1640px;width:260px;height:260px;border-radius:50%;background:radial-gradient(circle at 50% 40%,#5a6775,#c7dbe6 70%,var(--sky-soft))}
.pitem{position:absolute;width:200px;font-size:11px;color:var(--muted);line-height:1.6}
.pitem h4{font-size:15px;font-weight:600;color:var(--ink);margin-bottom:4px}
.pitem .more{color:var(--sky-deep);font-weight:600;margin-top:6px;font-size:11px}
.picon{position:absolute;width:44px;height:44px;border-radius:50%;background:var(--white);display:flex;align-items:center;justify-content:center;box-shadow:0 3px 10px rgba(22,166,224,.2)}

/* newsletter */
.news{left:0;top:2250px;width:1200px;height:420px;background:linear-gradient(180deg,#6fd2f6,#2fb6ec 60%,#56c7f2)}
.news h2{position:absolute;top:120px;width:1200px;text-align:center;color:var(--white);font-family:"Questrial",sans-serif;font-weight:400;font-size:32px}
.news p{position:absolute;top:165px;width:1200px;text-align:center;color:var(--white);font-size:12px}
.field{position:absolute;height:36px;border-radius:18px;background:var(--white);font-size:11px;color:var(--muted);display:flex;align-items:center;padding-left:18px}
.sub-bar{position:absolute;left:320px;top:2528px;width:560px;height:36px;border-radius:18px;background:var(--sky-deep);color:var(--white);font-size:12px;font-weight:600;display:flex;align-items:center;justify-content:center;border:1px solid rgba(255,255,255,.6)}

/* edge */
.card-img{position:absolute;top:2750px;height:245px;border-radius:6px}
.card h2{font-family:"Questrial",sans-serif;font-weight:400;font-size:34px;margin-bottom:10px}
.card{position:absolute;top:3010px;width:410px}

/* contact */
.contact{left:0;top:3290px;width:1200px;height:570px;background:linear-gradient(180deg,#8fdcf7,#3bbdf0 55%,#2aaee6)}
.contact h2{position:absolute;top:110px;width:1200px;text-align:center;color:var(--white);font-family:"Questrial",sans-serif;font-weight:400;font-size:36px}
.contact p{position:absolute;top:160px;width:1200px;text-align:center;color:var(--white);font-size:12px}
.cfield{position:absolute;left:370px;width:460px;height:32px;background:var(--white);border-radius:3px;font-size:11px;color:var(--muted);padding:9px 14px}

/* footer */
.footer{left:0;top:3880px;width:1200px;height:270px}
.fcol{position:absolute;top:50px;font-size:11px;color:var(--muted);line-height:1.9}
.fcol h5{font-size:14px;color:var(--sky-deep);font-weight:600;margin-bottom:6px}
.social{position:absolute;left:120px;top:210px;display:flex;gap:8px}
.social i{width:26px;height:26px;border-radius:50%;background:var(--sky);display:block}
.bottom{position:absolute;left:0;top:4150px;width:1200px;height:54px;background:var(--pale);font-size:11px;color:var(--muted);display:flex;align-items:center;justify-content:center}
</style>
</head>
<body>

<!-- navigation -->
<header class="nav">
  <div class="brand"><i></i>Corvana Real Estate</div>
  <nav class="menu"><span>Home</span><span>About Us</span><span>Our Businesses</span><span>Investors Lobby</span><span>News</span><span>Contact Us</span></nav>
  <div class="login">LOGIN</div>
</header>

<!-- hero -->
<div class="hero-bg"></div>
<div class="photo hero-photo" role="img" aria-label="Business team meeting around a conference table"></div>
<div class="play" style="left:250px;top:150px"><svg width="18" height="18" viewBox="0 0 18 18"><path d="M5 3l10 6-10 6z" fill="var(--sky)"/></svg></div>
<div class="abs hero-text">
  <div class="kicker">Global Private Equity Real Estate</div>
  <h1>Focused<br><em>Strategy,</em><br>Superior<br><em>Returns</em></h1>
</div>
<div class="btn" style="left:630px;top:520px">About Us<span class="dot"><svg width="12" height="12" viewBox="0 0 12 12"><path d="M3 6h6M6 3l3 3-3 3" stroke="var(--sky)" stroke-width="1.6" fill="none"/></svg></span></div>
<div class="abs play-video"><span class="play" style="position:relative;width:44px;height:44px"><svg width="14" height="14" viewBox="0 0 18 18"><path d="M5 3l10 6-10 6z" fill="var(--sky)"/></svg></span>Play Video</div>

<!-- stats -->
<div class="abs stats">
  <div class="stat"><b>4.6</b><small>M$ Million</small><span>Annual Revenues</span></div>
  <div class="stat"><b>265.59</b><small>M$ Million</small><span>Annual Operating Income</span></div>
  <div class="stat"><b>164</b><small>M$ Million</small><span>Annual Net Profit</span></div>
  <div class="stat"><b>1.2</b><small>M$ Billion</small><span>Equity</span></div>
</div>

<!-- about -->
<section class="abs about">
  <h3>About Us</h3>
  <h2>Corvana <span>Real Estate</span></h2>
  <p class="para">Lorem Ipsum has been the industry's standard dummy text ever since the 1500s, when an unknown printer took a galley of type and scrambled it to make a type specimen book. It has survived not only five centuries, but also the leap into electronic typesetting.</p>
  <ul class="checks">
    <li><i></i>Lorem Ipsum has been the industry's</li>
    <li><i></i>Lorem Ipsum has been the industry's</li>
    <li><i></i>Lorem Ipsum has been the industry's</li>
    <li><i></i>Lorem Ipsum has been the industry's</li>
  </ul>
</section>
<div class="btn" style="left:180px;top:1295px">Learn More<span class="dot"><svg width="12" height="12" viewBox="0 0 12 12"><path d="M3 6h6M6 3l3 3-3 3" stroke="var(--sky)" stroke-width="1.6" fill="none"/></svg></span></div>
<div class="photo about-art" role="img" aria-label="House and money bag balanced on a scale"></div>

<!-- investment platforms -->
<section class="abs platforms">
  <svg class="abs" style="left:0;top:700px" width="1200" height="240" viewBox="0 0 1200 240"><path d="M0 240 L0 120 Q600 -60 1200 120 L1200 240Z" fill="#3cc3f2" opacity=".35"/></svg>
  <h2>Our Investment <span>Platforms</span></h2>
</section>
<svg class="abs" style="left:340px;top:1540px" width="520" height="480" viewBox="0 0 520 480"><path d="M40 240 A220 220 0 0 1 480 240" stroke="var(--sky)" stroke-width="1.5" stroke-dasharray="4 5" fill="none"/><path d="M60 320 A220 220 0 0 0 460 320" stroke="var(--sky)" stroke-width="1.5" stroke-dasharray="4 5" fill="none"/><circle cx="120" cy="90" r="4" fill="var(--sky-deep)"/><circle cx="400" cy="90" r="4" fill="var(--sky-deep)"/></svg>
<div class="photo center-photo" role="img" aria-label="Businessman in a suit holding a calculator"></div>

<div class="picon" style="left:322px;top:1728px"><svg width="22" height="22" viewBox="0 0 22 22" fill="none" stroke="var(--sky-deep)" stroke-width="1.5"><rect x="3" y="6" width="9" height="13"/><rect x="12" y="10" width="7" height="9"/><path d="M6 10h3M6 14h3"/></svg></div>
<div class="pitem" style="left:110px;top:1712px"><h4>Multi Family</h4>Lorem Ipsum has been the industry's standard dummy text ever since the<div class="more">Read More →</div></div>

<div class="picon" style="left:820px;top:1728px"><svg width="22" height="22" viewBox="0 0 22 22" fill="none" stroke="var(--sky-deep)" stroke-width="1.5"><path d="M3 9l8-5 8 5z M5 10v7M9 10v7M13 10v7M17 10v7M3 19h16"/></svg></div>
<div class="pitem" style="left:912px;top:1712px"><h4>Capital</h4>Lorem Ipsum has been the industry's standard dummy text ever since the<div class="more">Read More →</div></div>

<div class="picon" style="left:510px;top:1916px"><svg width="22" height="22" viewBox="0 0 22 22" fill="none" stroke="var(--sky-deep)" stroke-width="1.5"><circle cx="11" cy="11" r="7"/><path d="M11 7v8M8.5 9h4a1.5 1.5 0 0 1 0 3h-3a1.5 1.5 0 0 0 0 3h4"/></svg></div>
<div class="pitem" style="left:200px;top:1940px"><h4>Debt</h4>Lorem Ipsum has been the industry's standard dummy text ever since the<div class="more">Read More →</div></div>

<div class="picon" style="left:735px;top:1916px"><svg width="22" height="22" viewBox="0 0 22 22" fill="none" stroke="var(--sky-deep)" stroke-width="1.5"><rect x="4" y="3" width="8" height="16"/><rect x="12" y="8" width="6" height="11"/><path d="M7 7h2M7 11h2M7 15h2"/></svg></div>
<div class="pitem" style="left:850px;top:1940px"><h4>Hospitality</h4>Lorem Ipsum has been the industry's standard dummy text ever since the<div class="more">Read More →</div></div>

<div class="picon" style="left:578px;top:1990px"><svg width="22" height="22" viewBox="0 0 22 22" fill="none" stroke="var(--sky-deep)" stroke-width="1.5"><path d="M3 11l8-7 8 7M5 10v9h12v-9M9 19v-5h4v5"/></svg></div>
<div class="pitem" style="left:510px;top:2045px;text-align:center"><h4>Single Family</h4>Lorem Ipsum has been the industry's standard dummy text ever since the<div class="more">Read More →</div></div>

<!-- newsletter -->
<section class="abs news">
  <svg class="abs" style="left:0;top:0" width="1200" height="120" viewBox="0 0 1200 120"><path d="M0 0 H1200 V40 Q600 140 0 40Z" fill="#d8f1fc"/></svg>
  <div class="abs" role="img" aria-label="City skyline seen from above in blue tones" style="left:0;top:60px;width:1200px;height:360px;background:linear-gradient(180deg,rgba(255,255,255,0),rgba(14,120,170,.25))"></div>
  <h2>Stay UpDated</h2>
  <p>Subscribe now to receive the latest updates on private investments</p>
</section>
<div class="field" style="left:320px;top:2470px;width:270px">Enter Name</div>
<div class="field" style="left:610px;top:2470px;width:270px">Enter Email</div>
<div class="sub-bar">SUBSCRIBE</div>

<!-- edge & responsibility -->
<div class="photo card-img" style="left:160px;width:400px;background:linear-gradient(135deg,#7db37a,#d4e7cb 50%,#5c8f5a)" role="img" aria-label="Hands holding a plant with sustainability icons"></div>
<div class="photo card-img" style="left:620px;width:415px;background:linear-gradient(135deg,#0d1f4a,#2a66c4 55%,#7ad4f5)" role="img" aria-label="Open book glowing with private equity lettering"></div>
<div class="card" style="left:160px"><h2>Our Edge</h2><p class="para">Lorem Ipsum has been the industry's standard dummy text ever since the 1500s, when an unknown printer took a galley of type and scrambled it to make a type specimen book. It has survived not only five centuries, but also the leap into electronic typesetting.</p></div>
<div class="card" style="left:620px"><h2>Our Responsibility</h2><p class="para">Lorem Ipsum has been the industry's standard dummy text ever since the 1500s, when an unknown printer took a galley of type and scrambled it to make a type specimen book. It has survived not only five centuries, but also the leap into electronic typesetting.</p></div>
<div class="btn" style="left:160px;top:3195px">Investor Information<span class="dot"><svg width="12" height="12" viewBox="0 0 12 12"><path d="M3 6h6M6 3l3 3-3 3" stroke="var(--sky)" stroke-width="1.6" fill="none"/></svg></span></div>
<div class="btn" style="left:620px;top:3195px">Read More<span class="dot"><svg width="12" height="12" viewBox="0 0 12 12"><path d="M3 6h6M6 3l3 3-3 3" stroke="var(--sky)" stroke-width="1.6" fill="none"/></svg></span></div>

<!-- contact -->
<section class="abs contact">
  <svg class="abs" style="left:0;top:0" width="1200" height="110" viewBox="0 0 1200 110"><path d="M0 0 H1200 V20 Q600 130 0 20Z" fill="#ffffff"/></svg>
  <h2>Contact Us</h2>
  <p>If you need any help, our team is ready to assist you</p>
</section>
<div class="cfield" style="top:3490px">Name*</div>
<div class="cfield" style="top:3536px">Email*</div>
<div class="cfield" style="top:3582px">Phone*</div>
<div class="cfield" style="top:3628px;height:90px">Message*</div>
<div class="btn" style="left:370px;top:3740px;background:var(--sky-deep)">Send<span class="dot"><svg width="12" height="12" viewBox="0 0 12 12"><path d="M3 6h6M6 3l3 3-3 3" stroke="var(--sky)" stroke-width="1.6" fill="none"/></svg></span></div>

<!-- footer -->
<footer class="abs footer">
  <div class="abs" style="left:130px;top:60px;width:110px;height:110px;border-radius:50%;background:var(--sky)"></div>
  <div class="social"><i></i><i></i><i></i><i></i></div>
  <div class="fcol" style="left:340px"><h5>Important Links</h5>Privacy Policy<br>Terms &amp; Conditions<br>Accessibility Statement<br>Contact Us</div>
  <div class="fcol" style="left:600px"><h5>Explore Corvana Real Estate</h5>About Us<br>Our Businesses<br>Investors Lobby<br>News<br>Contact Us</div>
  <div class="fcol" style="left:880px"><h5>Contact Us</h5>Corvana Real Estate<br>48 Harbour Lane, Suite 12<br>Westport, NV 00000<br>+1 555 014 2290<br>info@corvana-re.example</div>
</footer>
<div class="bottom">© Corvana Real Estate · 2024 All rights reserved. Terms &amp; Condition · Privacy Policy</div>

</body>
</html>
```